Lar Ventura Banners Ads

We need to create 4 animated banners ads in GIF (3 arts for each banner) to Lar Ventura Publiclik Display Campaign
Lar Ventura is an ecommerce in Brazil that sells high end home products.
It is a Branding Campaign, but we will add products images on it, so it has to be very sofisticated like the brand is.

We need 4 designs - 1 design for each size:

- Retângulo inline (300 X 250)
- Retângulo grande (336 x 280)
- Banner (468 x 60)
- Cabeçalho (728 x 90)

Please, find the briefing in pdf archive attached

Text we can work on th banners:

1 - Sofisticação com exclusividade para sua Casa!
2 - chique, exclusivo e encantador
3 - Encantador, sofisticado e exclusivo

The final image has to have Fontenelle´s Logo, Lar Ventura´s logo and a call to action:

Confira nossos produtos exclusivos!

_________________________________________________________________
UPDATE

Please, for the colors, take the ones from pdf; (use more collors chics, silver and white, but not only this colors);
Don't forget the CALL TO ACTION " Confira nossos Produtos Exclusivos!"

If you'd like to meet the brand and the target, here is the page on Facebook: https://www.rededeamigos.example/LarVenturaHomeVentura

But please, DO NOT COPY ANY OF THESE EXAMPLES ON THE PAGE.
We need something more executive.

Target Market(s)

Woman 30+
Trendy, modern, sofisticated, married or mum, cosmopolitan,
UPPERCLASS

Industry/Entity Type

Call

Font styles to use
Script
Other font styles liked:
• ColfaxTrial

Requirements
Must have
• Product images
Text
Product Image + Call to action on final layer with logos
As you will see the example in pdf archive attached
Nice to have
• frames
Should not have
• people
flowers
girlish drawing

```html
<!DOCTYPE html>
<html lang="pt-BR">
<head>
<meta charset="utf-8">
<title>Lar Ventura — Banners Display</title>
<link href="https://fonts.googleapis.com/css2?family=Heebo:wght@500;700&display=swap" rel="stylesheet">
<style>
  :root {
    --stage: #ece7e1;
    --white: #ffffff;
    --green: #9acb3c;
    --pink: #de3f96;
    --pink-light: #ec5ea8;
    --pink-dark: #b82a75;
    --logo: #8b8178;
    --linen-light: #dcdde1;
    --linen-mid: #b8bcc3;
    --linen-pink: #e9cfd6;
  }
  * { margin: 0; padding: 0; box-sizing: border-box; }
  html, body { width: 1200px; height: 900px; overflow: hidden; }
  body {
    background: var(--stage);
    font-family: "Heebo", Arial, sans-serif;
    position: relative;
  }
  .banner {
    position: absolute;
    overflow: hidden;
    transform-origin: 0 0;
    transform: scale(1.171875);
    background: var(--green);
  }
  .banner svg.shapes { position: absolute; inset: 0; }
  .brand-name {
    position: absolute;
    color: var(--logo);
    font-weight: 500;
    letter-spacing: 0.02em;
    white-space: nowrap;
    text-align: center;
  }
  .headline {
    position: absolute;
    color: var(--white);
    font-weight: 700;
    text-align: center;
    line-height: 1.05;
  }
  .cta {
    position: absolute;
    display: flex;
    align-items: center;
    background: linear-gradient(180deg, var(--pink-light), var(--pink));
    border-radius: 4px;
    box-shadow: 0 2px 3px rgba(0,0,0,0.3);
    color: var(--white);
    font-weight: 700;
    white-space: nowrap;
  }
  .cta-icon {
    flex: none;
    border-radius: 50%;
    background: var(--pink-dark);
    display: flex;
    align-items: center;
    justify-content: center;
  }
  .cta-icon svg { width: 70%; height: 70%; }

  /* Cabeçalho 728x90 */
  .leaderboard { left: 217px; top: 182px; width: 728px; height: 90px; }
  .leaderboard .brand-name { left: 4px; top: 30px; width: 140px; font-size: 22px; }
  .leaderboard .headline { left: 190px; top: 8px; width: 240px; font-size: 21px; }
  .leaderboard .cta { left: 447px; top: 30px; width: 164px; height: 37px; font-size: 17px; padding-left: 5px; gap: 8px; }
  .leaderboard .cta-icon { width: 29px; height: 29px; }

  /* Banner 468x60 */
  .banner-468 { left: 418px; top: 348px; width: 468px; height: 60px; }
  .banner-468 .brand-name { left: 2px; top: 19px; width: 92px; font-size: 15px; }
  .banner-468 .headline { left: 115px; top: 6px; width: 166px; font-size: 13.5px; }
  .banner-468 .cta { left: 287px; top: 20px; width: 106px; height: 24px; font-size: 11px; padding-left: 3px; gap: 5px; }
  .banner-468 .cta-icon { width: 19px; height: 19px; }

  /* Retângulo inline 300x250 */
  .rect-300 { left: 315px; top: 500px; width: 300px; height: 250px; }
  .rect-300 .brand-name { left: 0; top: 4px; width: 300px; font-size: 36px; }
  .rect-300 .headline { left: 0; top: 110px; width: 142px; font-size: 15px; line-height: 1.45; }
  .rect-300 .cta { left: 4px; top: 205px; width: 144px; height: 33px; font-size: 15px; padding-left: 4px; gap: 7px; }
  .rect-300 .cta-icon { width: 26px; height: 26px; }

  /* Retângulo grande 336x280 */
  .rect-336 { left: 731px; top: 483px; width: 336px; height: 280px; }
  .rect-336 .brand-name { left: 0; top: 5px; width: 336px; font-size: 40px; }
  .rect-336 .headline { left: 0; top: 122px; width: 158px; font-size: 17px; line-height: 1.45; }
  .rect-336 .cta { left: 4px; top: 230px; width: 166px; height: 37px; font-size: 17px; padding-left: 5px; gap: 8px; }
  .rect-336 .cta-icon { width: 29px; height: 29px; }
</style>
</head>
<body>

<svg width="0" height="0" style="position:absolute">
  <defs>
    <linearGradient id="linen" x1="0" y1="0" x2="1" y2="1">
      <stop offset="0" stop-color="#e6e4e6"/>
      <stop offset="0.35" stop-color="#e9cfd6"/>
      <stop offset="0.6" stop-color="#b8bcc3"/>
      <stop offset="1" stop-color="#9aa0a8"/>
    </linearGradient>
    <symbol id="cart" viewBox="0 0 24 24">
      <path d="M2 4h3l2.2 10h11l2-7H6.2" fill="none" stroke="#fff" stroke-width="2.2" stroke-linejoin="round" stroke-linecap="round"/>
      <circle cx="9" cy="19" r="1.8" fill="#fff"/>
      <circle cx="17" cy="19" r="1.8" fill="#fff"/>
    </symbol>
  </defs>
</svg>

<!-- Cabeçalho -->
<section class="banner leaderboard">
  <svg class="shapes" viewBox="0 0 728 90" width="728" height="90">
    <polygon points="0,0 168,0 130,90 0,90" fill="var(--white)"/>
    <line x1="168" y1="0" x2="130" y2="90" stroke="var(--pink)" stroke-width="4"/>
    <polygon points="623,0 728,0 728,90 585,90" fill="url(#linen)" role="img" aria-label="Product photo: made bed with grey linens and pink pillows"/>
    <line x1="623" y1="0" x2="585" y2="90" stroke="var(--pink)" stroke-width="4"/>
  </svg>
  <div class="brand-name">Lar Ventura</div>
  <p class="headline">Sofisticação com exclusividade para sua Casa!</p>
  <div class="cta"><span class="cta-icon"><svg><use href="#cart"/></svg></span>ADD TO CART</div>
</section>

<!-- Banner -->
<section class="banner banner-468">
  <svg class="shapes" viewBox="0 0 468 60" width="468" height="60">
    <polygon points="0,0 107,0 84,60 0,60" fill="var(--white)"/>
    <line x1="107" y1="0" x2="84" y2="60" stroke="var(--pink)" stroke-width="3"/>
    <polygon points="393,0 468,0 468,60 369,60" fill="url(#linen)" role="img" aria-label="Product photo: made bed with grey linens and pink pillows"/>
    <line x1="393" y1="0" x2="369" y2="60" stroke="var(--pink)" stroke-width="3"/>
  </svg>
  <div class="brand-name">Lar Ventura</div>
  <p class="headline">Sofisticação com exclusividade para sua Casa!</p>
  <div class="cta"><span class="cta-icon"><svg><use href="#cart"/></svg></span>ADD TO CART</div>
</section>

<!-- Retângulo inline -->
<section class="banner rect-300">
  <svg class="shapes" viewBox="0 0 300 250" width="300" height="250">
    <rect x="0" y="0" width="300" height="52" fill="var(--white)"/>
    <polygon points="176,52 300,52 300,250 100,250" fill="url(#linen)" role="img" aria-label="Product photo: bed with grey quilted linens and pink pillows"/>
    <line x1="176" y1="52" x2="100" y2="250" stroke="var(--pink)" stroke-width="3"/>
  </svg>
  <div class="brand-name">Lar Ventura</div>
  <p class="headline">chique, exclusivo<br>e encantador</p>
  <div class="cta"><span class="cta-icon"><svg><use href="#cart"/></svg></span>ADD TO CART</div>
</section>

<!-- Retângulo grande -->
<section class="banner rect-336">
  <svg class="shapes" viewBox="0 0 336 280" width="336" height="280">
    <rect x="0" y="0" width="336" height="58" fill="var(--white)"/>
    <polygon points="192,58 336,58 336,280 112,280" fill="url(#linen)" role="img" aria-label="Product photo: bed with grey quilted linens and pink pillows"/>
    <line x1="192" y1="58" x2="112" y2="280" stroke="var(--pink)" stroke-width="3"/>
  </svg>
  <div class="brand-name">Lar Ventura</div>
  <p class="headline">chique, exclusivo<br>e encantador</p>
  <div class="cta"><span class="cta-icon"><svg><use href="#cart"/></svg></span>ADD TO CART</div>
</section>

</body>
</html>
```